NZ First of it's kind solutions directory and marketplace for busy Mums needs a business card design

We need a business card design for our new nationwide business in NZ (long term plans to go global). We provide solutions to the everyday challenges that busy Mums face by connecting them with quality communities and suppliers of carefully selected, relevant products and services. We sell direct via our online marketplace. The final design should communicate our values of inclusivity, quality and smart solutions. Colours should incorporate our logo colour palette of #477077 and #6ba8b2. Our website is at https://www.brightnestmums.example

Target Market(s)

busy Mums, Age 28 – 50, female, income over $100K, location main centres NZ primarily but NZ wide. Is likely juggling work or career with a young family. Probably had hobbies which have fallen by the wayside.
-Wants to succeed in her chosen career without compromising on family life
-to successfully juggle her career without feeling like she is compromising her children
- Is time poor, something always has to give and it’s generally her health (she’ll stay up late, get stressed)
- probably ex corporate or professional career. Has discretional income

Industry/Entity Type

Business

Contact Information for Business Card

Lena Forbisher, Founder, BrightNestMums.example (Strapline Tap; Gather; Sorted), 47 Kowhai Terrace, Ellerslie, Auckland 1051, New Zealand. Mob: 021 483 517 Ph: +64 (0)9 571 4860

Font styles to use
Other font styles liked:
• Raleway, and/or Architects Daughter

Colors
00a990
33b8a4
86cfc6
cfeae6

Requirements
Must have
• the above details, streamline. the logo and colours associated with those logos
Should not have
• foil or metallic colours

```html
<!DOCTYPE html>
<html lang="en">
<head>
<meta charset="UTF-8">
<title>BrightNestMums – Business Card</title>
<link href="https://fonts.googleapis.com/css2?family=Raleway:wght@400;500;700;800&display=swap" rel="stylesheet">
<style>
  :root {
    --bg: #e4e4e2;
    --card-white: #ffffff;
    --brand-dark: #477077;
    --brand-light: #6ba8b2;
    --teal: #00a98f;
    --wave: #45bfa5;
    --text-white: #ffffff;
    --mint: #cfeae6;
  }
  * { margin: 0; padding: 0; box-sizing: border-box; }
  html, body {
    width: 1200px; height: 1000px; overflow: hidden;
    background: var(--bg);
    font-family: "Raleway", sans-serif;
  }
  .canvas { position: relative; width: 1200px; height: 1000px; }

  .card { position: absolute; overflow: hidden; box-shadow: 0 14px 28px rgba(0,0,0,.28); }

  /* Front */
  .card-front { left: 170px; top: 112px; width: 590px; height: 336px; background: var(--card-white); }
  .card-front .wave { position: absolute; left: 0; top: 0; width: 590px; height: 336px; }
  .front-brand {
    position: absolute; left: 100px; top: 130px;
    display: flex; align-items: center; gap: 14px;
  }
  .brand-dot { width: 40px; height: 40px; border-radius: 50%; background: var(--brand-dark); }
  .front-brand .brand-name {
    font-weight: 800; font-size: 44px; color: var(--brand-dark); letter-spacing: -0.5px;
  }

  /* Back */
  .card-back { left: 390px; top: 558px; width: 600px; height: 342px; background: var(--teal); color: var(--text-white); }
  .person { position: absolute; left: 48px; top: 70px; }
  .person-name { font-size: 27px; font-weight: 400; line-height: 1.2; }
  .person-role { font-size: 18px; font-weight: 400; margin-top: 6px; }
  .back-brand {
    position: absolute; right: 40px; top: 80px;
    display: flex; align-items: center; gap: 8px;
  }
  .back-brand .brand-dot { width: 26px; height: 26px; background: var(--mint); }
  .back-brand .brand-name { font-weight: 800; font-size: 24px; color: var(--text-white); }
  .divider { position: absolute; left: 0; top: 165px; width: 600px; height: 2px; background: var(--text-white); }
  .address-tab {
    position: absolute; left: 58px; top: 166px; width: 488px; height: 26px;
    background: var(--card-white); border-radius: 0 0 14px 14px;
    color: var(--teal); font-size: 15px; font-weight: 500;
    display: flex; align-items: center; justify-content: center;
  }
  .contact-list { position: absolute; left: 46px; top: 212px; list-style: none; }
  .contact-list li { display: flex; align-items: center; height: 32px; font-size: 18px; }
  .contact-list svg { width: 20px; height: 20px; margin-right: 16px; flex: none; }
  .strapline { font-size: 12px; margin-left: 6px; }
</style>
</head>
<body>
<main class="canvas">

  <section class="card card-front" aria-label="Card front">
    <svg class="wave" viewBox="0 0 590 336" aria-hidden="true">
      <path d="M0,226 C110,205 200,240 290,285 C370,318 460,220 590,220 L590,336 L0,336 Z" fill="var(--wave)"/>
    </svg>
    <div class="front-brand">
      <span class="brand-dot"></span>
      <span class="brand-name">BrightNestMums</span>
    </div>
  </section>

  <section class="card card-back" aria-label="Card back">
    <div class="person">
      <p class="person-name">Lena Forbisher</p>
      <p class="person-role">Founder</p>
    </div>
    <div class="back-brand">
      <span class="brand-dot"></span>
      <span class="brand-name">BrightNestMums</span>
    </div>
    <div class="divider"></div>
    <div class="address-tab">47 Kowhai Terrace, Ellerslie, Auckland 1051, New Zealand</div>
    <ul class="contact-list">
      <li>
        <svg viewBox="0 0 24 24" aria-hidden="true"><path fill="#fff" d="M3 8c0-2 4-4 9-4s9 2 9 4v2h-5V8c-1-.6-2.5-1-4-1s-3 .4-4 1v2H3zM6 12h12l2 8H4z"/><circle cx="12" cy="16" r="2" fill="var(--teal)"/></svg>
        <span>+64 (0)9 571 4860</span>
      </li>
      <li>
        <svg viewBox="0 0 24 24" aria-hidden="true"><path fill="#fff" d="M6.6 10.8c1.4 2.8 3.8 5.1 6.6 6.6l2.2-2.2c.3-.3.7-.4 1-.2 1.1.4 2.3.6 3.6.6.6 0 1 .4 1 1V20c0 .6-.4 1-1 1C10.6 21 3 13.4 3 4c0-.6.4-1 1-1h3.5c.6 0 1 .4 1 1 0 1.3.2 2.5.6 3.6.1.3 0 .7-.2 1z"/></svg>
        <span>021 483 517</span>
      </li>
      <li>
        <svg viewBox="0 0 24 24" aria-hidden="true" fill="none" stroke="#fff" stroke-width="2"><circle cx="12" cy="12" r="9"/><ellipse cx="12" cy="12" rx="4" ry="9"/><path d="M3 12h18M5 7h14M5 17h14"/></svg>
        <span>www.brightnestmums.example<span class="strapline">( Strapline Tap; Gather; Sorted )</span></span>
      </li>
    </ul>
  </section>

</main>
</body>
</html>
```